IT Support Business needs a Flyer Designed

Have just had new logo and business cards made for new business called Byte Harbor, am now in need of a new flyer design. Byte Harbor will be providing home and small business it support.
Updates
Byte Harbor flyer design brief has been uploaded. The contest has also been changed to payment guaranteed.
If you need anymore information please feel free to contact myself.
Project Deadline Extended
Reason: I signed up early to take advantage of the artfolly 24 hour sale, and was a few days late in providing a design brief. Therefore I am extending the deadline by 2 days, to ensure it lasts for a good 2 weeks.
Have worked on and refined the Design Brief a bit more, hoping it makes it a bit clearer as to what I want on the flyer. If you have any questions please do not hesitate to ask.
I have refined the design brief overnight, after receiving some feedback, please refer to newly uploaded file for this morning. I am hoping it makes things clearer and easier.
Industry/Entity Type
Small Business

```html
<!DOCTYPE html>
<html lang="en">
<head>
<meta charset="utf-8">
<title>Byte Harbor Flyer</title>
<link href="https://fonts.googleapis.com/css2?family=Open+Sans:wght@400;600;700&family=Exo+2:ital,wght@1,600&display=swap" rel="stylesheet">
<style>
  :root {
    --navy: #25307a;
    --navy-deep: #1b2466;
    --blue: #2f58a8;
    --red: #d4231f;
    --orange: #ee5a24;
    --grey-text: #5a5e66;
    --caption: #2b2f3a;
    --paper: #ffffff;
    --mist: #e7eaf1;
    --stage: #ebe9e5;
  }
  * { margin: 0; padding: 0; box-sizing: border-box; }
  html, body { width: 1200px; height: 448px; overflow: hidden; }
  body {
    background: var(--stage);
    font-family: "Open Sans", Arial, sans-serif;
    position: relative;
  }
  .flyer {
    position: absolute;
    width: 552px;
    height: 354px;
    background: linear-gradient(170deg, var(--paper) 0%, var(--mist) 45%, var(--paper) 70%);
    overflow: hidden;
    box-shadow: 0 2px 6px rgba(0,0,0,.25);
  }
  .flyer--front { left: 34px; top: 30px; }
  .flyer--back { left: 617px; top: 61px; }
  .flyer svg.swoosh { position: absolute; left: 0; top: 0; z-index: 1; }
  .flyer > p, .flyer > .brand, .flyer > .services { z-index: 2; }

  .brand {
    position: absolute;
    display: flex;
    align-items: center;
    gap: 6px;
    font-weight: 700;
    color: var(--navy);
    white-space: nowrap;
  }
  .brand__dot { width: 13px; height: 13px; border-radius: 50%; background: var(--orange); flex: none; }

  /* front */
  .intro {
    position: absolute; left: 17px; top: 28px; width: 392px;
    font-size: 11.4px; font-weight: 700; line-height: 1.38; color: var(--navy);
  }
  .flyer--front .brand { left: 420px; top: 56px; font-size: 16px; }
  .specialises {
    position: absolute; left: 33px; top: 90px;
    font-size: 12px; font-weight: 700; letter-spacing: 4.2px; color: var(--red);
  }
  .services { position: absolute; left: 0; top: 116px; width: 552px; height: 90px; }
  .service {
    position: absolute; top: 0;
    display: flex; flex-direction: column; align-items: center; text-align: center;
  }
  .service__icon {
    width: 30px; height: 30px; border-radius: 6px;
    background: linear-gradient(145deg, #6fb4e6, #2a6fb8 60%, #6cbf57);
    margin-bottom: 8px;
  }
  .service__text { font-size: 7.8px; line-height: 1.3; color: var(--caption); }
  .keyboard-photo {
    position: absolute; left: 190px; top: 196px; width: 362px; height: 140px; z-index: 0;
    background: radial-gradient(ellipse at 48% 45%, #7d7d7d 0%, #b2b2b2 40%, rgba(233,233,233,0) 75%);
  }
  .tagline {
    position: absolute; left: 0; right: 0; bottom: 12px; text-align: center;
    font-family: "Exo 2", Arial, sans-serif; font-style: italic; font-weight: 600;
    font-size: 14.6px; color: #fff;
  }

  /* back */
  .coverage {
    position: absolute; left: 16px; top: 24px; width: 268px;
    font-size: 10.8px; font-weight: 700; line-height: 1.45; color: var(--red);
  }
  .fees {
    position: absolute; left: 16px; top: 116px; width: 192px;
    font-size: 12.8px; font-weight: 700; line-height: 1.5; color: var(--navy);
  }
  .fees__price { color: var(--red); font-size: 16px; }
  .devices-photo {
    position: absolute; left: 196px; top: 50px; width: 348px; height: 166px; z-index: 0;
    background: radial-gradient(ellipse at 55% 55%, #6a6e76 0%, #a4a9b2 42%, rgba(230,232,238,0) 72%);
  }
  .flyer--back .brand { left: 30px; top: 262px; font-size: 18px; }
  .callout {
    position: absolute; left: 152px; top: 228px;
    font-family: "Exo 2", Arial, sans-serif; font-style: italic; font-weight: 600;
    font-size: 13.2px; line-height: 1.36; color: var(--grey-text);
  }
  .callout__name { color: var(--red); font-size: 14.6px; }
  .abn { position: absolute; right: 24px; top: 298px; font-size: 9.6px; color: #fff; }
  .contact {
    position: absolute; color: #fff; display: flex; align-items: center; gap: 4px;
  }
  .contact--phone { left: 20px; top: 322px; font-size: 17px; font-weight: 700; }
  .contact--place { left: 194px; top: 330px; font-size: 10px; }
  .contact--email { right: 24px; top: 317px; font-size: 10px; }
  .contact--web { right: 24px; top: 333px; font-size: 10px; }
  .contact svg { flex: none; }
</style>
</head>
<body>

<section class="flyer flyer--front">
  <div class="keyboard-photo" role="img" aria-label="Black and white photo of a hand typing on a keyboard"></div>

  <svg class="swoosh" width="552" height="354" viewBox="0 0 552 354" aria-hidden="true">
    <defs>
      <linearGradient id="frontBand" x1="0" y1="0" x2="0" y2="1">
        <stop offset="0" stop-color="#3d6cc0"/>
        <stop offset="1" stop-color="#1b2466"/>
      </linearGradient>
    </defs>
    <path d="M0 252 C140 276 300 316 552 302 L552 354 L0 354 Z" fill="url(#frontBand)"/>
    <path d="M0 222 C140 238 300 292 552 290 L552 300 C300 308 140 264 0 246 Z" fill="#d4231f"/>
    <path d="M0 250 C140 270 300 314 552 302" fill="none" stroke="#fff" stroke-width="3"/>
  </svg>

  <p class="intro">With over 15 years experience in the IT sector, Daniel from Byte Harbor provides friendly, reliable and professional service, supporting you to build your skills and knowledge to maximise your IT requirements.</p>

  <div class="brand"><span class="brand__dot"></span>Byte Harbor</div>

  <p class="specialises">Byte Harbor specialises in:</p>

  <div class="services">
    <div class="service" style="left:22px;width:60px"><div class="service__icon" role="img" aria-label="Computer repair tools icon"></div><p class="service__text">Computer repair, service installation and upgrades</p></div>
    <div class="service" style="left:94px;width:62px"><div class="service__icon" role="img" aria-label="Networked computers icon"></div><p class="service__text">Support to set up and secure your home network</p></div>
    <div class="service" style="left:163px;width:76px"><div class="service__icon" role="img" aria-label="Desktop computer icon"></div><p class="service__text">Sharing the tricks and tips to manage your new operating system</p></div>
    <div class="service" style="left:249px;width:58px"><div class="service__icon" role="img" aria-label="Software install icon"></div><p class="service__text">Assistance in installing and configuring new software</p></div>
    <div class="service" style="left:316px;width:104px"><div class="service__icon" role="img" aria-label="Internet globe icon"></div><p class="service__text">Getting you connected online and across social media faster, including Internet, email, VoiceLink, FriendSpace etc</p></div>
    <div class="service" style="left:428px;width:40px"><div class="service__icon" role="img" aria-label="Data backup icon"></div><p class="service__text">Data backup and recovery</p></div>
    <div class="service" style="left:478px;width:54px"><div class="service__icon" role="img" aria-label="Tuition people icon"></div><p class="service__text">Tuition in programs and technology</p></div>
  </div>

  <p class="tagline">Providing solutions for all your computer and technical equipment needs</p>
</section>

<section class="flyer flyer--back">
  <div class="devices-photo" role="img" aria-label="Photo of computers, laptops, printers and other devices"></div>

  <svg class="swoosh" width="552" height="354" viewBox="0 0 552 354" aria-hidden="true">
    <defs>
      <linearGradient id="backBand" x1="0" y1="0" x2="0" y2="1">
        <stop offset="0" stop-color="#3d6cc0"/>
        <stop offset="1" stop-color="#1b2466"/>
      </linearGradient>
    </defs>
    <path d="M0 314 L552 314 L552 354 L0 354 Z" fill="url(#backBand)"/>
    <path d="M290 314 C400 300 480 280 552 262 L552 314 Z" fill="url(#backBand)"/>
    <path d="M270 308 C380 296 470 268 552 244 L552 254 C470 280 390 302 270 308 Z" fill="#ee5a24"/>
  </svg>

  <p class="coverage">Our services and expertise extends across PC's, Laptops, printers, scanners, routers, tablet, mobile phone, cameras, television and arcade consoles, with the ability to work onsite or remotely as required.</p>

  <p class="fees">Byte Harbor service fees start at <span class="fees__price">$40</span> per hour however packages and flexible pricing for more complex tasks are available.</p>

  <div class="brand"><span class="brand__dot"></span>Byte Harbor</div>

  <p class="callout">With no call out fee, talk to <span class="callout__name">Daniel</span> today<br>to solve your IT and technology challenges.</p>

  <p class="abn">ABN is 12345678901</p>

  <p class="contact contact--phone">
    <svg width="16" height="16" viewBox="0 0 16 16" aria-hidden="true"><circle cx="8" cy="8" r="7" fill="none" stroke="#fff" stroke-width="1.3"/><path d="M5.5 4.5 L7 6 L6.2 7.2 C6.8 8.4 7.6 9.2 8.8 9.8 L10 9 L11.5 10.5 L10.6 11.6 C7.6 11.2 4.8 8.4 4.4 5.4 Z" fill="#fff"/></svg>
    0400 123 456
  </p>
  <p class="contact contact--place">
    <svg width="8" height="11" viewBox="0 0 8 11" aria-hidden="true"><path d="M4 0 C6.2 0 8 1.8 8 4 C8 6.5 4 11 4 11 C4 11 0 6.5 0 4 C0 1.8 1.8 0 4 0 Z" fill="#fff"/><circle cx="4" cy="4" r="1.5" fill="#25307a"/></svg>
    Kelvale, Victoria
  </p>
  <p class="contact contact--email">
    <svg width="11" height="8" viewBox="0 0 11 8" aria-hidden="true"><rect x="0.5" y="0.5" width="10" height="7" fill="none" stroke="#fff"/><path d="M0.5 0.5 L5.5 4.5 L10.5 0.5" fill="none" stroke="#fff"/></svg>
    daniel@byteharbor.com.au
  </p>
  <p class="contact contact--web">
    <svg width="10" height="10" viewBox="0 0 10 10" aria-hidden="true"><circle cx="5" cy="5" r="4.5" fill="none" stroke="#fff"/><ellipse cx="5" cy="5" rx="2" ry="4.5" fill="none" stroke="#fff"/><path d="M0.5 5 H9.5" stroke="#fff"/></svg>
    www.byteharbor.com.au
  </p>
</section>

</body>
</html>
```